Boutique custom software development company needs new business card

Our nearly 20 year old custom software development company would like to better include the fact that we are now providing Bitcoin services. These new services are B2B include education (how to acquire and securely hold Bitcoin) and integrating Bitcoin payments into existing ecommerce sites or other existing systems. Please keep the card clean and simple. Attached is our current design and some other files. vextorial.com

Target Market(s)

businesses owners interested in long term relationship

Industry/Entity Type

Custom software development and Bitcoin

Contact Information for Business Card

Dale Parker, dale@vextorial.com, vextorial.com, (888) 555-VXTRL

Font styles to use
Other font styles liked:
• monospace

Requirements
Must have
• double-sided
Nice to have
• clean and simple
Should not have
• physical address

```html
<!DOCTYPE html>
<html lang="en">
<head>
<meta charset="utf-8">
<title>Vextorial Business Card</title>
<link rel="stylesheet" href="https://fonts.googleapis.com/css2?family=Source+Sans+3:wght@400;600;700&display=swap">
<style>
  :root {
    --backdrop: #1f1f1f;
    --card: #ffffff;
    --brand-blue: #3d72b8;
    --brand-orange: #f07c22;
    --ink-light: #ffffff;
  }
  * { box-sizing: border-box; margin: 0; padding: 0; }
  html, body { width: 1200px; height: 1200px; overflow: hidden; }
  body {
    background: var(--backdrop);
    font-family: "Source Sans 3", "Source Sans Pro", Arial, sans-serif;
    position: relative;
  }
  .card {
    position: absolute;
    left: 250px;
    width: 700px;
    height: 400px;
    border-radius: 20px;
    background: var(--card);
    overflow: hidden;
  }
  .card--front { top: 170px; }
  .card--back { top: 631px; }

  .front-shapes { position: absolute; inset: 0; width: 700px; height: 400px; }

  .front-brand {
    position: absolute;
    left: 111px;
    top: 118px;
    display: flex;
    align-items: center;
    gap: 12px;
  }
  .front-brand__square {
    width: 40px;
    height: 40px;
    background: var(--brand-blue);
  }
  .front-brand__name {
    font-weight: 700;
    font-size: 30px;
    letter-spacing: 1px;
    color: var(--brand-blue);
  }

  .contact-block {
    position: absolute;
    right: 63px;
    top: 196px;
    text-align: right;
    color: var(--ink-light);
  }
  .contact-block__name {
    font-weight: 700;
    font-size: 29px;
    letter-spacing: 1.2px;
    line-height: 1;
    text-transform: uppercase;
  }
  .contact-block__title {
    font-size: 18px;
    letter-spacing: 0.5px;
    margin-top: 4px;
  }
  .contact-list {
    list-style: none;
    margin-top: 18px;
  }
  .contact-list__item {
    display: flex;
    justify-content: flex-end;
    align-items: center;
    gap: 10px;
    font-size: 16.5px;
    letter-spacing: 0.4px;
    height: 25px;
  }
  .contact-list__icon { width: 14px; height: 14px; flex: none; }

  .back-brand {
    position: absolute;
    left: 0;
    right: 0;
    top: 122px;
    text-align: center;
  }
  .back-brand__name {
    font-weight: 700;
    font-size: 84px;
    line-height: 1;
    letter-spacing: 2px;
    color: var(--brand-blue);
  }
  .back-brand__tagline {
    margin-top: 10px;
    font-size: 27px;
    letter-spacing: -1px;
    color: var(--brand-blue);
  }
  .back-services {
    position: absolute;
    left: 0;
    right: 0;
    top: 300px;
    text-align: center;
    font-weight: 600;
    font-size: 17px;
    letter-spacing: 1.5px;
    text-transform: uppercase;
    color: var(--brand-orange);
  }
</style>
</head>
<body>
  <section class="card card--front">
    <svg class="front-shapes" viewBox="0 0 700 400" aria-hidden="true">
      <polygon points="0,0 63,0 0,97" fill="var(--brand-orange)"/>
      <polygon points="490,0 700,0 700,400 230,400" fill="var(--brand-blue)"/>
    </svg>

    <div class="front-brand">
      <span class="front-brand__square"></span>
      <span class="front-brand__name">VEXTORIAL</span>
    </div>

    <div class="contact-block">
      <h1 class="contact-block__name">Dale Parker</h1>
      <p class="contact-block__title">Founding Partner</p>
      <ul class="contact-list">
        <li class="contact-list__item">
          <span>(888) 555-VXTRL</span>
          <svg class="contact-list__icon" viewBox="0 0 24 24" aria-hidden="true">
            <path fill="#fff" d="M6.6 10.8a15 15 0 0 0 6.6 6.6l2.2-2.2c.3-.3.7-.4 1-.2 1.1.4 2.3.6 3.6.6.6 0 1 .4 1 1V20c0 .6-.4 1-1 1C10.6 21 3 13.4 3 4c0-.6.4-1 1-1h3.5c.6 0 1 .4 1 1 0 1.3.2 2.5.6 3.6.1.3 0 .7-.2 1z"/>
          </svg>
        </li>
        <li class="contact-list__item">
          <span>dale@vextorial.com</span>
          <svg class="contact-list__icon" viewBox="0 0 24 24" aria-hidden="true">
            <rect x="2" y="5" width="20" height="14" fill="#fff"/>
            <path d="M2 5l10 8 10-8" fill="none" stroke="var(--brand-blue)" stroke-width="1.8"/>
          </svg>
        </li>
        <li class="contact-list__item">
          <span>vextorial.com</span>
          <svg class="contact-list__icon" viewBox="0 0 24 24" aria-hidden="true">
            <circle cx="12" cy="12" r="10" fill="#fff"/>
            <path d="M12 2v20M2 12h20M12 2c-4 4-4 16 0 20M12 2c4 4 4 16 0 20" fill="none" stroke="var(--brand-blue)" stroke-width="1.5"/>
          </svg>
        </li>
      </ul>
    </div>
  </section>

  <section class="card card--back">
    <div class="back-brand">
      <p class="back-brand__name">VEXTORIAL</p>
      <p class="back-brand__tagline">developer of custom applications</p>
    </div>
    <p class="back-services">Bitcoin education &amp; payment integration</p>
  </section>
</body>
</html>
```